Industrial Project Sign

We need an eye catching (but professional) industrial project sign that will be very large (roughly 12' high x 18' wide). This sign will be highly visible from the adjacent high speed highway.

* The following needs to be at the bottom of the signage: Logo (uploaded), Name (Brightline Property Partners, Inc.) (uploaded) and phone number (415)736-2958

*Name of Project - "Meridale Commerce Park"

* Text items
Land for Sale
Build to Suit
Zoning: Industrial (G I & L I)

* Interesting background that is eye catching
Updates

Good morning all,

We are considering all designers options as we go and are waiting for the final designs to come in by the 4th so that we can give each one a good look.   If you have any new designs, questions, further design options or any tweeks you want to do to current designs, please do so at this time.

Thanks to all of you for your submissions.

Industry/Entity Type

Industrial

```html
<!DOCTYPE html>
<html lang="en">
<head>
<meta charset="utf-8">
<title>Meridale Commerce Park – Project Sign</title>
<link rel="stylesheet" href="https://fonts.googleapis.com/css2?family=Open+Sans:wght@400;600;700&family=Montserrat:wght@800;900&display=swap">
<style>
  :root {
    --ink: #111111;
    --title-ink: #3a3a3a;
    --accent: #6b1519;
    --panel-light: #ececec;
    --panel-mid: #b4b4b4;
    --panel-dark: #707070;
    --band: rgba(255, 255, 255, 0.82);
    --white: #ffffff;
  }
  * { margin: 0; padding: 0; box-sizing: border-box; }
  html, body { width: 1200px; height: 800px; overflow: hidden; background: var(--white); }
  .sign {
    position: relative;
    width: 1200px;
    height: 800px;
    overflow: hidden;
    font-family: "Open Sans", sans-serif;
  }
  .site-photo {
    position: absolute;
    inset: 0;
    background:
      radial-gradient(ellipse 260px 200px at 1010px 110px, rgba(232, 150, 60, 0.55), transparent 70%),
      radial-gradient(ellipse 340px 260px at 1080px 560px, rgba(200, 214, 230, 0.9), transparent 70%),
      radial-gradient(ellipse 220px 300px at 760px 640px, rgba(150, 130, 110, 0.45), transparent 70%),
      linear-gradient(180deg, #dfe8ef 0%, #e9e4dc 45%, #c9c3bb 100%);
  }
  .side-panel {
    position: absolute;
    inset: 0;
  }
  .title-band {
    position: absolute;
    left: 0; top: 0;
    width: 1200px; height: 100px;
    background: linear-gradient(180deg, rgba(255,255,255,0.55), rgba(255,255,255,0.15));
  }
  .project-name {
    position: absolute;
    top: 22px; left: 0; width: 1200px;
    text-align: center;
    font-family: "Open Sans", sans-serif;
    font-weight: 700;
    font-size: 58px;
    line-height: 1;
    letter-spacing: 1px;
    color: var(--title-ink);
    text-transform: uppercase;
    text-shadow: 2px 2px 3px rgba(0,0,0,0.35);
  }
  .title-rule {
    position: absolute;
    top: 88px; left: 135px;
    width: 910px; height: 3px;
    background: linear-gradient(90deg, transparent, #555 15%, #555 85%, transparent);
  }
  .feature-band {
    position: absolute;
    left: 575px; top: 205px;
    width: 625px; height: 390px;
    background: var(--band);
  }
  .feature-list {
    position: absolute;
    left: 665px; top: 245px;
    list-style: none;
  }
  .feature-list li {
    position: relative;
    padding-left: 48px;
    font-family: "Montserrat", sans-serif;
    font-weight: 900;
    font-size: 41px;
    line-height: 1;
    color: var(--ink);
    text-transform: uppercase;
    margin-bottom: 56px;
  }
  .feature-list li::before {
    content: "";
    position: absolute;
    left: 0; top: 12px;
    width: 20px; height: 18px;
    background: var(--accent);
    clip-path: polygon(25% 0, 75% 0, 100% 50%, 75% 100%, 25% 100%, 0 50%);
  }
  .feature-detail {
    display: block;
    margin-top: 12px;
    font-family: "Open Sans", sans-serif;
    font-weight: 600;
    font-size: 35px;
  }
  .company {
    position: absolute;
    left: 60px; top: 402px;
    display: flex;
    align-items: center;
    gap: 16px;
  }
  .company-mark {
    width: 26px; height: 26px;
    background: var(--accent);
  }
  .company-name {
    font-family: "Open Sans", sans-serif;
    font-weight: 600;
    font-size: 23px;
    color: var(--ink);
  }
  .phone-icon {
    position: absolute;
    left: 262px; top: 542px;
  }
  .phone-number {
    position: absolute;
    left: 60px; top: 596px;
    font-family: "Open Sans", sans-serif;
    font-weight: 700;
    font-size: 66px;
    line-height: 1;
    color: var(--accent);
    text-shadow: 1px 2px 2px rgba(0,0,0,0.3);
  }
  .website {
    position: absolute;
    left: 20px; top: 758px;
    font-family: "Open Sans", sans-serif;
    font-weight: 700;
    font-size: 19px;
    color: var(--white);
    text-transform: uppercase;
  }
</style>
</head>
<body>
<main class="sign">
  <div class="site-photo" role="img" aria-label="Blurred photo of a construction site with an engineer in a hard hat and white shirt, arms crossed, and workers behind"></div>

  <svg class="side-panel" width="1200" height="800" viewBox="0 0 1200 800" aria-hidden="true">
    <defs>
      <linearGradient id="panel-fill" x1="0" y1="0" x2="1" y2="1">
        <stop offset="0" stop-color="var(--panel-light)"/>
        <stop offset="0.5" stop-color="var(--panel-mid)"/>
        <stop offset="1" stop-color="var(--panel-dark)"/>
      </linearGradient>
    </defs>
    <polygon points="0,0 480,0 670,410 465,800 0,800" fill="url(#panel-fill)"/>
  </svg>

  <div class="title-band"></div>
  <h1 class="project-name">Meridale Commerce Park</h1>
  <div class="title-rule"></div>

  <div class="feature-band"></div>
  <ul class="feature-list">
    <li>Land for Sale</li>
    <li>Build to Suit</li>
    <li>Zoning:<span class="feature-detail">Industrial (G I &amp; L I)</span></li>
  </ul>

  <div class="company">
    <span class="company-mark"></span>
    <span class="company-name">Brightline Property Partners, Inc.</span>
  </div>

  <svg class="phone-icon" width="34" height="50" viewBox="0 0 34 50" aria-hidden="true">
    <path d="M10 2 L16 14 L11 18 C12 26 16 32 22 36 L27 32 L33 42 L26 48 C12 44 2 28 3 8 Z" fill="var(--accent)"/>
  </svg>
  <p class="phone-number">(415)736-2958</p>

  <p class="website">www.brightlinepropertypartners.com</p>
</main>
</body>
</html>
```